Business Card for Lantern Reach

Please design a Modern Business card for a Online Marketing Company

Website: http://www.lanternreach-example.com.au

Please do NOT include physical address in design.

```html
<!DOCTYPE html>
<html lang="en">
<head>
<meta charset="utf-8">
<title>Lantern Reach – Business Card</title>
<link href="https://fonts.googleapis.com/css2?family=Open+Sans:wght@400;700&display=swap" rel="stylesheet">
<style>
  :root {
    --brand-red: #c10a1c;
    --accent-orange: #f28a0f;
    --ink-dark: #2b2b2b;
    --ink-soft: #3c3c3c;
    --paper: #ffffff;
    --backdrop: #ececec;
  }
  * { box-sizing: border-box; margin: 0; padding: 0; }
  html, body { width: 1200px; height: 483px; overflow: hidden; }
  body {
    background: var(--backdrop);
    display: flex;
    align-items: center;
    justify-content: center;
    gap: 60px;
    font-family: "Open Sans", sans-serif;
  }
  .card {
    position: relative;
    width: 520px;
    height: 300px;
    overflow: hidden;
    box-shadow: 0 6px 18px rgba(0,0,0,0.25);
  }

  /* Front face */
  .card-front { background: var(--paper); }
  .front-swoosh { position: absolute; inset: 0; width: 100%; height: 100%; }
  .holder {
    position: absolute;
    top: 20px;
    left: 0;
    width: 100%;
    text-align: center;
    color: var(--paper);
    font-size: 17px;
    letter-spacing: 0.5px;
  }
  .holder strong { font-weight: 700; font-size: 21px; letter-spacing: 1px; }
  .wordmark {
    position: absolute;
    top: 138px;
    left: 190px;
  }
  .wordmark-name {
    font-weight: 700;
    font-size: 24px;
    color: var(--brand-red);
    line-height: 1.1;
    letter-spacing: 0.3px;
  }
  .tagline {
    font-weight: 700;
    font-size: 13px;
    color: var(--ink-dark);
    margin-top: 2px;
  }
  .contacts {
    position: absolute;
    right: 40px;
    bottom: 28px;
    list-style: none;
    font-size: 14px;
    color: var(--ink-soft);
    line-height: 1.8;
  }
  .contacts li { display: flex; align-items: center; justify-content: flex-end; gap: 7px; }
  .contacts svg { width: 12px; height: 12px; fill: var(--ink-soft); }

  /* Back face */
  .card-back {
    background: var(--brand-red);
    color: var(--paper);
  }
  .back-name {
    position: absolute;
    top: 96px;
    left: 0;
    width: 100%;
    text-align: center;
    font-weight: 700;
    font-size: 44px;
    line-height: 1;
  }
  .back-tagline {
    position: absolute;
    top: 150px;
    left: 0;
    width: 100%;
    text-align: center;
    padding-left: 70px;
    font-weight: 700;
    font-size: 20px;
  }
  .back-web {
    position: absolute;
    bottom: 38px;
    width: 100%;
    text-align: center;
    font-size: 17px;
    letter-spacing: 0.5px;
  }
</style>
</head>
<body>

  <section class="card card-front" aria-label="Card front">
    <svg class="front-swoosh" viewBox="0 0 520 300" preserveAspectRatio="none" aria-hidden="true">
      <path d="M0 0 H520 V62 Q280 58 0 152 Z" fill="var(--brand-red)"/>
      <path d="M0 168 Q280 74 520 80" fill="none" stroke="var(--accent-orange)" stroke-width="6"/>
    </svg>
    <p class="holder"><strong>Your Name</strong>, Title</p>
    <div class="wordmark">
      <p class="wordmark-name">LANTERN REACH</p>
      <p class="tagline">Be seen online - Grow online</p>
    </div>
    <ul class="contacts">
      <li>
        <svg viewBox="0 0 24 24" aria-hidden="true"><path d="M6.6 10.8a15.1 15.1 0 0 0 6.6 6.6l2.2-2.2c.3-.3.7-.4 1-.2 1.1.4 2.3.6 3.6.6.6 0 1 .4 1 1V20c0 .6-.4 1-1 1C10.6 21 3 13.4 3 4c0-.6.4-1 1-1h3.5c.6 0 1 .4 1 1 0 1.3.2 2.5.6 3.6.1.3 0 .7-.2 1z"/></svg>
        0400 555 019
      </li>
      <li>
        <svg viewBox="0 0 24 24" aria-hidden="true"><path d="M2 5h20v14H2z M2 5l10 8 10-8"/></svg>
        plan@lanternreach-example.com.au
      </li>
      <li>
        <svg viewBox="0 0 24 24" aria-hidden="true"><circle cx="12" cy="12" r="10"/></svg>
        www.lanternreach-example.com.au
      </li>
    </ul>
  </section>

  <section class="card card-back" aria-label="Card back">
    <p class="back-name">LANTERN REACH</p>
    <p class="back-tagline">Be seen online - Grow online</p>
    <p class="back-web">www.lanternreach-example.com.au</p>
  </section>

</body>
</html>
```